Business card design for a teacher - double sided, sleek design.

My name is Lina and I am an online Arabic language teacher. I am looking for a beautiful business card design for my online teaching business.

The cards will be printed in 85mm x 55mm size.
The card can be either portrait or landscape.

The design should contain my logo on one side and information on the other.

The design needs to be clean and modern. Use of subtle Arabic geometric patterns would be nice. Icons for the social media information on the card should also match the design theme.

My logo font is Consolas, which is a Monospace font.

Business card design should be delivered with editable PSD or EPS files in the handover.

Thanks

Lina

----

Information on the back:

URL: www.speakwithnadia.net [this should stand out more than other details]
Email: info@speakwithnadia.net
Instagram: @speakwithnadia
Facebook: facebook.com/speakwithnadia
Skype: speakwithnadia

My brand colours are shown in the logo attached. These are:
- Teal green - 4DC9C1
- Mango yellow - FFD600

Target Market(s)

- Young professionals
- Expatriates
- Women and Men

Industry/Entity Type

Education

Contact Information for Business Card

Information on the back:

Skype: speakwithnadia

- Teal green - 4DC9C1
- Mango yellow - FFD600

Font styles to use
Other font styles liked:
• Any font complimentary to my logo font which is a Monospace font called Consolas.

Colors

Designer to choose colors to be used in the design.

Requirements
Must have
• - Aesthetically pleasing look
• - Complimentary design with existing logo
Nice to have
• Arabic geometrical patterns

```html
<!DOCTYPE html>
<html lang="en">
<head>
<meta charset="utf-8">
<title>Arabic with Lina — Business Card</title>
<link rel="stylesheet" href="https://fonts.googleapis.com/css2?family=Inconsolata:wght@500&family=Roboto:wght@400&display=swap">
<style>
  :root {
    --teal: #4dc9c1;
    --mango: #ffd600;
    --ink: #555555;
    --ink-dark: #5a5a5a;
    --paper: #f4f4f2;
    --pattern-tone: #eaf5f1;
    --stage: #2b2b2b;
  }
  * { margin: 0; padding: 0; box-sizing: border-box; }
  html, body {
    width: 1200px; height: 960px; overflow: hidden;
    background: var(--stage);
  }
  .card {
    position: absolute;
    width: 600px; height: 342px;
    overflow: hidden;
  }
  /* Information side */
  .card--info { left: 314px; top: 113px; background: var(--paper); }
  .info-frame {
    position: absolute; left: 30px; top: 28px;
    width: 547px; height: 288px;
    border: 6px solid var(--mango);
  }
  .brand-name {
    position: absolute; left: 14px; top: 60px;
    font-family: "Inconsolata", monospace; font-weight: 500;
    font-size: 50px; line-height: 58px;
    color: var(--teal);
    background: var(--paper);
    padding: 6px 14px 6px 6px;
  }
  .contact-list {
    position: absolute; right: 72px; top: 177px;
    list-style: none; text-align: right;
    font-family: "Roboto", sans-serif; font-size: 14px;
    line-height: 19.3px; color: var(--ink);
  }
  .contact-list li { position: relative; }
  .contact-list li::after {
    content: ""; position: absolute;
    right: -19px; top: 4px; width: 11px; height: 11px;
    background: var(--teal);
  }
  .contact-list li.contact--web::after { border-radius: 50%; }

  /* Logo side */
  .card--logo { left: 311px; top: 472px; background: var(--paper); }
  .logo-pattern {
    position: absolute; inset: 0;
    background: linear-gradient(135deg, var(--pattern-tone), #f3f4ea);
  }
  .logo-lockup {
    position: absolute; left: 165px; top: 118px;
    display: flex; align-items: center; gap: 22px;
  }
  .logo-square {
    width: 94px; height: 102px;
    border: 4px solid var(--mango);
  }
  .logo-name {
    font-family: "Inconsolata", monospace; font-weight: 500;
    font-size: 40px; line-height: 34px; letter-spacing: 3px;
    color: var(--ink-dark); text-transform: uppercase;
  }
  .logo-name .with { display: block; font-size: 12px; line-height: 16px; text-align: center; }
  .card-url {
    position: absolute; left: 0; right: 0; top: 292px;
    text-align: center;
    font-family: "Roboto", sans-serif; font-size: 14px;
    letter-spacing: 4px; color: var(--ink);
  }
</style>
</head>
<body>
  <section class="card card--info">
    <div class="info-frame"></div>
    <div class="brand-name">Arabic<br>with<br>Lina</div>
    <ul class="contact-list">
      <li class="contact--email">info@speakwithnadia.net</li>
      <li class="contact--instagram">@speakwithnadia</li>
      <li class="contact--facebook">facebook.com/speakwithnadia</li>
      <li class="contact--skype">speakwithnadia</li>
      <li class="contact--web">www.speakwithnadia.net</li>
    </ul>
  </section>

  <section class="card card--logo">
    <div class="logo-pattern" role="img" aria-label="Subtle repeating Arabic geometric pattern in pale teal and yellow"></div>
    <div class="logo-lockup">
      <div class="logo-square"></div>
      <div class="logo-name">Arabic<span class="with">with</span>Lina</div>
    </div>
    <p class="card-url">www.speakwithnadia.net</p>
  </section>
</body>
</html>
```